International oil and gas consultancy needs a business card design

We need a business card design for a new oil and gas consultancy business based in Perth Australia. This is a professional services business and needs a moderately conservative type of business card. The business card also needs to be simple and uncluttered. The colour of the business logo is dark red (see attached file).
The front of the card should have a white background and mainly black lettering and perhaps some use of dark red and/or grey (your choice).
The back of the card should have a light grey background with dark red, black and or both dark red & black lettering (your choice).
Please find attached a clear brief of how I would like the business card designed.
Updates

Hello Everyone, I have slightly modified the brief. The main change is to incorporate some dark red and grey colours into the card, while still keeping the black lettering dominant. I have made the changes in the attached detailed brief document. Regards

Please note, the front of the card must say Harbour Ledger Services (in addition to the logo).

Industry/Entity Type

Conservative

Requirements
Must have
• brief has been updated. please refer to attachment for details.

Front of the card MUST say Harbour Ledger Services (in addition to the logo)

```html
<!DOCTYPE html>
<html lang="en">
<head>
<meta charset="UTF-8">
<title>Harbour Ledger Services – Business Card</title>
<link rel="stylesheet" href="https://fonts.googleapis.com/css2?family=Saira:wght@400;500;600&display=swap">
<style>
  :root {
    --stage: #b9bfc7;
    --card-white: #f7f7f7;
    --card-shade: #dcdcdc;
    --brand-red: #961c1f;
    --ink: #2b2b2b;
    --on-red: #ffffff;
  }
  * { box-sizing: border-box; margin: 0; padding: 0; }
  html, body { width: 1200px; height: 864px; overflow: hidden; }
  body {
    background: var(--stage);
    font-family: "Saira", sans-serif;
    position: relative;
  }
  .card {
    position: absolute;
    width: 520px;
    height: 300px;
    background: linear-gradient(135deg, var(--card-white) 0%, #efefef 55%, var(--card-shade) 100%);
    box-shadow: 0 10px 30px rgba(0,0,0,0.18);
    overflow: hidden;
  }
  .card--brand { left: 70px; top: 120px; }
  .card--contact { left: 610px; top: 440px; }

  .brand-name {
    color: var(--brand-red);
    font-weight: 600;
    letter-spacing: 0.5px;
    line-height: 1.05;
  }
  .card--brand .brand-name {
    position: absolute;
    left: 0; right: 0; top: 50%;
    transform: translateY(-50%);
    text-align: center;
    font-size: 38px;
  }
  .card--contact .brand-name {
    position: absolute;
    left: 34px; top: 82px;
    width: 250px;
    font-size: 26px;
  }

  .wave { position: absolute; inset: 0; width: 100%; height: 100%; }
  .wave path { fill: var(--brand-red); }

  .holder {
    position: absolute;
    left: 34px; top: 176px;
    color: var(--ink);
  }
  .holder__name { font-size: 20px; font-weight: 500; letter-spacing: 1px; text-transform: uppercase; }
  .holder__role { font-size: 14px; font-weight: 400; margin-top: -2px; }

  .contact {
    position: absolute;
    right: 22px; top: 44px;
    list-style: none;
    color: var(--on-red);
    text-align: right;
    font-size: 11px;
    line-height: 1.35;
  }
  .contact li {
    display: flex;
    justify-content: flex-end;
    align-items: center;
    gap: 6px;
    margin-bottom: 11px;
  }
  .contact svg { width: 10px; height: 10px; flex: none; fill: none; stroke: var(--on-red); stroke-width: 1.6; }
</style>
</head>
<body>

  <section class="card card--brand" aria-label="Card back">
    <p class="brand-name">Harbour Ledger Services</p>
  </section>

  <section class="card card--contact" aria-label="Card front">
    <svg class="wave" viewBox="0 0 520 300" preserveAspectRatio="none" aria-hidden="true">
      <path d="M360 0 L520 0 L520 300 L60 300 C190 300 290 260 318 150 C338 70 336 10 360 0 Z"/>
    </svg>

    <p class="brand-name">Harbour Ledger Services</p>

    <div class="holder">
      <p class="holder__name">Daniel Marlow</p>
      <p class="holder__role">Managing Director</p>
    </div>

    <ul class="contact">
      <li><span>041 12th floor, Quay Tower<br>Riverside Road WA</span>
        <svg viewBox="0 0 10 10"><path d="M5 9 C2 6 2 4.5 2 4 A3 3 0 0 1 8 4 C8 4.5 8 6 5 9 Z"/><circle cx="5" cy="4" r="1"/></svg></li>
      <li><span>018 442 7310</span>
        <svg viewBox="0 0 10 10"><path d="M2 1 L4 1 L4.6 3.4 L3.4 4.2 C4 5.6 4.6 6.2 6 6.8 L6.8 5.6 L9 6.2 L9 8.2 C5 8.6 1.4 5 2 1 Z"/></svg></li>
      <li><span>018 442 7311</span>
        <svg viewBox="0 0 10 10"><rect x="2.5" y="0.8" width="5" height="8.4" rx="1"/></svg></li>
      <li><span>018 442 7312</span>
        <svg viewBox="0 0 10 10"><rect x="1.5" y="3.5" width="7" height="5"/><path d="M3 3.5 V1 H7 V3.5"/></svg></li>
      <li><span>info@hlservices.com</span>
        <svg viewBox="0 0 10 10"><rect x="1" y="2" width="8" height="6"/><path d="M1 2 L5 5.5 L9 2"/></svg></li>
      <li><span>www.hlservices.com</span>
        <svg viewBox="0 0 10 10"><circle cx="5" cy="5" r="4"/><path d="M1 5 H9 M5 1 C3 3.5 3 6.5 5 9 M5 1 C7 3.5 7 6.5 5 9"/></svg></li>
    </ul>
  </section>

</body>
</html>
```